Road Construction Company needs business cards

We would like a new business card designed for our business.

We're a road construction company based in Qld, Australia.

Can the business card please have the following information on it.

Name: Warren Halbeck
Position: General Manager
Phone: 0472 915 348
Email: Warren.halbeck@tovrin.com.au
Address: 87 Marrow Ave, Pendlebay, QLD, 4023
Website: www.tovrin.com.au

Visually we'd like the card to be professional and simple.

Attached is our logo.

Our website is www.tovrin.com.au

Target Market(s)

Men aged 25-60

Contact Information for Business Card

As listed in project description

Font styles to use
Serif

Requirements
Must have
• Large logo on back of card

```html
<!DOCTYPE html>
<html lang="en">
<head>
<meta charset="utf-8">
<title>Tovrin Business Card</title>
<link rel="stylesheet" href="https://fonts.googleapis.com/css2?family=Inter:wght@400;800&display=swap">
<style>
  :root {
    --backdrop: #9a9a9a;
    --brand-blue: #0b55a1;
    --brand-navy: #0f2f6d;
    --brand-sky: #2fa6dc;
    --name-blue: #0b4ea2;
    --text-grey: #4a4a4a;
    --card-white: #ffffff;
  }
  * { margin: 0; padding: 0; box-sizing: border-box; }
  html, body {
    width: 1021px;
    height: 1200px;
    overflow: hidden;
    background: var(--backdrop);
    font-family: "Inter", Arial, sans-serif;
  }
  .card {
    position: absolute;
    left: 138px;
    width: 745px;
    height: 426px;
    overflow: hidden;
  }
  .card-front {
    top: 121px;
    background: var(--brand-blue);
    display: flex;
    align-items: center;
    justify-content: center;
  }
  .front-wordmark {
    font-weight: 800;
    font-size: 88px;
    letter-spacing: 12px;
    color: var(--brand-navy);
    margin-top: -30px;
    line-height: 1;
  }
  .card-back {
    top: 651px;
    background: var(--card-white);
  }
  .back-wordmark {
    position: absolute;
    left: 43px;
    top: 184px;
    font-weight: 800;
    font-size: 62px;
    letter-spacing: 7px;
    color: var(--brand-blue);
    line-height: 1;
  }
  .divider {
    position: absolute;
    left: 376px;
    top: 114px;
    width: 2px;
    height: 188px;
    background: var(--brand-blue);
  }
  .contact {
    position: absolute;
    left: 393px;
    top: 110px;
    color: var(--text-grey);
    font-size: 19.5px;
    line-height: 26px;
  }
  .contact-name {
    font-weight: 800;
    font-size: 27px;
    line-height: 32px;
    color: var(--name-blue);
    text-transform: uppercase;
  }
  .contact-title { margin-bottom: 12px; }
  .contact-address { margin-bottom: 22px; }
  .contact-line { display: flex; align-items: center; gap: 6px; }
  .contact-line svg { flex: none; }
  .footer-band {
    position: absolute;
    left: 0;
    bottom: 0;
    width: 100%;
    height: 46px;
    background: var(--brand-blue);
    border-top: 5px solid var(--brand-sky);
    display: flex;
    align-items: center;
    justify-content: flex-end;
    padding-right: 40px;
  }
  .website {
    color: var(--card-white);
    font-size: 19px;
  }
</style>
</head>
<body>
  <section class="card card-front">
    <div class="front-wordmark">TOVRIN</div>
  </section>

  <section class="card card-back">
    <div class="back-wordmark">TOVRIN</div>
    <div class="divider"></div>
    <div class="contact">
      <div class="contact-name">Warren Halbeck</div>
      <div class="contact-title">General Manager</div>
      <div class="contact-address">87 Marrow Ave<br>Pendlebay, QLD, 4023</div>
      <div class="contact-line">
        <svg width="18" height="18" viewBox="0 0 24 24" aria-hidden="true"><path fill="var(--brand-sky)" d="M6.6 10.8a15 15 0 0 0 6.6 6.6l2.2-2.2a1 1 0 0 1 1-.25 11.4 11.4 0 0 0 3.6.57 1 1 0 0 1 1 1V20a1 1 0 0 1-1 1A17 17 0 0 1 3 4a1 1 0 0 1 1-1h3.5a1 1 0 0 1 1 1c0 1.25.2 2.45.57 3.6a1 1 0 0 1-.25 1z"/></svg>
        <span>0472 915 348</span>
      </div>
      <div class="contact-line">
        <svg width="18" height="14" viewBox="0 0 24 18" aria-hidden="true"><rect x="1" y="1" width="22" height="16" rx="2" fill="var(--brand-sky)"/><path d="M2 3l10 7 10-7" fill="none" stroke="#fff" stroke-width="2"/></svg>
        <span>Warren.halbeck@tovrin.com.au</span>
      </div>
    </div>
    <div class="footer-band">
      <span class="website">www.tovrin.com.au</span>
    </div>
  </section>
</body>
</html>
```